'Keep Your Light Burning, Young Ones'

This 40 page booklet (A5 format = A4 page folded) is aimed at TEENAGERS at risk. New Zealand has a very high teen suicide rate, so this booklet cover design needs to be colorful, bold and evye catching for teenagers.

Target Market(s)

Teenagers

Industry/Entity Type

High School students

Requirements
Must have
• A colorful bold design to grab the attention of teens
Nice to have
• The cover could include a generic photo of a teen or group of teens, OR a stylised graphic
Should not have
• not too many words. Short author bio supplied on request: Marcus Feltham had a difficult upbringing. He has battled low self-esteem and depression most of his life BUT he has always found a way through and learned to process the pain of bullying and abuse.'

```html
<!DOCTYPE html>
<html lang="en">
<head>
<meta charset="utf-8">
<title>Keep Your Light Burning, Young Ones — Back Cover</title>
<link rel="stylesheet" href="https://fonts.googleapis.com/css2?family=Lilita+One&family=Dosis:wght@800&family=Kaushan+Script&family=Montserrat:wght@500;600&display=swap">
<style>
  :root {
    --backdrop: #d9d9d9;
    --paper: #ffffff;
    --red: #e31013;
    --green: #1fa009;
    --teal: #10a1b8;
    --orange: #f07810;
    --indigo: #3a0788;
    --yellow: #ffed00;
    --violet: #9b00c8;
    --white: #ffffff;
  }
  * { margin: 0; padding: 0; box-sizing: border-box; }
  html, body {
    width: 1200px; height: 1200px; overflow: hidden;
    background: var(--backdrop);
  }
  .cover {
    position: absolute; left: 425px; top: 351px;
    width: 355px; height: 504px;
    background: var(--paper);
  }
  .title {
    position: absolute; left: 0; top: 30px; width: 100%;
    text-align: center; line-height: 1;
  }
  .title__lead {
    display: block;
    font-family: "Lilita One", sans-serif;
    font-size: 38px; color: var(--red);
    letter-spacing: 0.5px;
  }
  .title__bold {
    display: block; margin-top: 4px;
    font-family: "Dosis", sans-serif; font-weight: 800;
    font-size: 34px; color: var(--green);
    letter-spacing: 0.5px;
  }
  .title__script {
    display: block; margin-top: 0;
    font-family: "Kaushan Script", cursive;
    font-size: 40px; color: var(--teal);
    line-height: 1.1;
  }
  .title__audience {
    display: block; margin-top: 2px;
    font-family: "Dosis", sans-serif; font-weight: 800;
    font-size: 16px; color: var(--orange);
  }
  .blurb {
    position: absolute; left: 45px; top: 222px;
    width: 262px; height: 188px;
    border-radius: 40px; background: var(--orange);
    padding: 8px;
  }
  .blurb__ring {
    width: 100%; height: 100%;
    border-radius: 32px; background: var(--indigo);
    padding: 8px;
  }
  .blurb__band {
    width: 100%; height: 100%;
    border-radius: 25px; background: var(--yellow);
    padding: 8px;
  }
  .blurb__panel {
    width: 100%; height: 100%;
    border-radius: 18px; background: var(--violet);
    padding: 12px 11px 0 12px;
  }
  .blurb__text {
    font-family: "Montserrat", sans-serif; font-weight: 600;
    font-size: 7.6px; line-height: 9.15px;
    color: var(--white); text-align: justify;
    hyphens: auto;
  }
  .web-link {
    position: absolute; left: 22px; top: 456px;
    width: 111px; height: 21px;
    border-radius: 7px; background: var(--violet);
    display: flex; align-items: center; gap: 5px;
    padding-left: 3px;
    font-family: "Montserrat", sans-serif; font-weight: 500;
    font-size: 7.4px; color: var(--white);
  }
  .web-link__icon { width: 15px; height: 15px; flex: none; }
  .code-slot {
    position: absolute; background: var(--violet);
  }
  .code-slot--square { left: 201px; top: 421px; width: 49px; height: 56px; border-radius: 12px; }
  .code-slot--wide { left: 258px; top: 436px; width: 72px; height: 41px; border-radius: 8px; }
</style>
</head>
<body>
  <main class="cover">
    <h1 class="title">
      <span class="title__lead">KEEP YOUR</span>
      <span class="title__bold">LIGHT</span>
      <span class="title__script">Burning</span>
      <span class="title__audience">Young Ones</span>
    </h1>

    <section class="blurb">
      <div class="blurb__ring">
        <div class="blurb__band">
          <div class="blurb__panel">
            <p class="blurb__text">Lorem ipsum dolor sit amet, consectetuer adipiscing elit, sed diam nonummy nibhation ullamcorper suscipit lobortis nisl ut aliquip ex ea commodo consequat. Duis autem vel eum iriure dolor in hendrerit in vulputate velit esse molestie consequat, vel illum dolore eu feugiat nulla facilisis at vero eros et accumsan et iusto odio dignissim qui blandit praesent luptatum zzril delenit augue duis dolore te feugait nulla facilisi. Lorem ipsum dolor sit amet, cons ectetuer adipiscing elit, sed diam nonummy nibh euismod tincidunt ut laoreet dolore magna aliquam erat volutpat. Ut wisi enim ad minim</p>
          </div>
        </div>
      </div>
    </section>

    <div class="web-link">
      <svg class="web-link__icon" viewBox="0 0 16 16" aria-hidden="true">
        <circle cx="8" cy="8" r="8" fill="#ffffff"/>
        <g fill="none" stroke="#9b00c8" stroke-width="0.9">
          <circle cx="8" cy="8" r="4.6"/>
          <ellipse cx="8" cy="8" rx="2" ry="4.6"/>
          <line x1="3.4" y1="8" x2="12.6" y2="8"/>
          <line x1="4" y1="5.8" x2="12" y2="5.8"/>
          <line x1="4" y1="10.2" x2="12" y2="10.2"/>
        </g>
      </svg>
      <span>WWW.XXXXXXX.COM</span>
    </div>

    <div class="code-slot code-slot--square"></div>
    <div class="code-slot code-slot--wide"></div>
  </main>
</body>
</html>
```